menu board design: rustle burger

we are a burger restaurant.
we need to re design our menu board to fit within the new design of the restaurant. we are after something simple and easy to read. the overall look and feel of the design should be inline with the design of the shop.

Target Market(s)

18-40 male and female

Colors

Designer to choose colors to be used in the design.

Requirements
Must have
• easy to read. good layout. white background. branding included in design.

```html
<!DOCTYPE html>
<html lang="en">
<head>
<meta charset="utf-8">
<title>Rustle Burger Menu Board</title>
<link rel="stylesheet" href="https://fonts.googleapis.com/css2?family=Amatic+SC:wght@400;700&family=Fredoka:wght@600&family=Roboto:wght@400;500&display=swap">
<style>
:root{
  --blue:#1f4fa6;
  --blue-deep:#1a449a;
  --orange:#f7941d;
  --paper:#f5f5f4;
  --ink:#3b3b3b;
}
*{margin:0;padding:0;box-sizing:border-box}
html,body{width:1200px;height:690px;overflow:hidden;background:var(--paper)}
.board{position:relative;width:1200px;height:690px;background:var(--paper);font-family:"Amatic SC",cursive;font-weight:700;color:var(--blue)}
.abs{position:absolute}

.banner{position:absolute;top:45px;width:252px;height:62px}
.banner svg{position:absolute;inset:0}
.banner h2{position:relative;text-align:center;line-height:62px;color:#fff;font-size:42px;font-weight:700;letter-spacing:1px}
.banner.beef{left:26px}
.banner.chicken{left:300px}

.column{position:absolute;top:123px;width:238px;height:533px;border-left:1px solid var(--orange);border-bottom:1px solid var(--orange)}
.column.beef{left:35px}
.column.chicken{left:311px}
.intro{position:absolute;left:26px;top:8px;width:190px;font-family:"Roboto",sans-serif;font-size:8px;line-height:10.5px;color:var(--ink)}
.double{position:absolute;left:20px;top:63px;width:196px;height:34px}
.double svg{position:absolute;inset:0}
.double span{position:relative;display:block;text-align:center;line-height:34px;font-size:22px;font-weight:700}

.item{position:absolute;left:26px;width:182px}
.item .line{display:flex;align-items:baseline;font-size:26px;line-height:26px;font-weight:700}
.item .line .dots{flex:1;border-bottom:2px dotted var(--blue);margin:0 3px 5px}
.item p{font-family:"Roboto",sans-serif;font-weight:500;font-size:7.5px;line-height:10px;color:var(--ink);margin-top:5px}

.side-band{left:571px;top:0;width:629px;height:187px}
.side-badge{left:704px;top:33px;width:170px;height:170px;border-radius:50%;background:var(--orange);display:flex;align-items:center;justify-content:center;font-family:"Fredoka",sans-serif;font-size:50px;color:#fff;letter-spacing:2px}
.side-list{left:905px;top:36px;width:236px;color:#fff}
.side-list .line{display:flex;align-items:baseline;font-size:28px;line-height:34px}
.side-list .dots{flex:1;border-bottom:2px dotted #fff;margin:0 3px 8px}
.side-list p{font-size:19px;line-height:25px;margin-top:6px}

.stars{background:linear-gradient(180deg,rgba(31,79,166,.12),rgba(31,79,166,.05));border-radius:10px}
.stars.orange{background:linear-gradient(90deg,rgba(247,148,29,.14),rgba(247,148,29,.06))}

.brand{left:548px;top:540px;width:128px;display:flex;align-items:center;gap:6px;font-size:34px;line-height:34px;font-weight:700}
.brand .dot{width:11px;height:11px;border-radius:50%;background:var(--blue);flex:none}

.heading{font-family:"Fredoka",sans-serif;font-size:36px;letter-spacing:2px;text-align:center;line-height:1}
.nachos-title{left:666px;top:232px;width:504px}
.box{position:absolute;border:1.5px dashed var(--blue);padding:8px 10px}
.step-title{font-size:30px;text-align:center;border-bottom:1px solid var(--orange);margin:4px 50px 6px 20px;padding-bottom:4px}
.step{position:absolute;top:-8px;right:-8px;width:52px;height:52px;border-radius:50%;background:var(--orange);color:#fff;font-family:"Fredoka",sans-serif;font-size:13px;line-height:14px;text-align:center;display:flex;align-items:center;justify-content:center}
.choice .line{display:flex;align-items:baseline;font-size:24px;line-height:30px}
.choice .dots{flex:1;border-bottom:2px dotted var(--blue);margin:0 3px 7px}
.loaded p{font-size:18px;line-height:22px;text-align:center}
.loaded p b{color:var(--orange);font-weight:700}

.ribs-title{left:666px;top:456px;width:504px}
.ribs-copy{left:700px;top:504px;width:440px;text-align:center;font-size:18px;line-height:22px}
.packs .line{display:flex;align-items:baseline;font-size:25px;line-height:30px}
.packs .dots{flex:1;border-bottom:2px dotted var(--blue);margin:0 3px 7px}
.sauces{display:flex;align-items:center;justify-content:center;text-align:center;font-size:25px;line-height:31px}
</style>
</head>
<body>
<main class="board">

  <div class="banner beef">
    <svg viewBox="0 0 252 62" preserveAspectRatio="none"><polygon points="0,2 252,6 238,31 252,57 4,61 16,31" fill="var(--blue)"/></svg>
    <h2>Beef Burgers</h2>
  </div>
  <div class="banner chicken">
    <svg viewBox="0 0 252 62" preserveAspectRatio="none"><polygon points="0,2 252,6 238,31 252,57 4,61 16,31" fill="var(--blue)"/></svg>
    <h2>Chicken Burgers</h2>
  </div>

  <section class="column beef">
    <p class="intro">All Our Patties Are 100% Natural Beef. We Know Because We Grind It Ourselves. Smashed To Order On A Hot Grill Right In Front Of You.</p>
    <div class="double">
      <svg viewBox="0 0 196 34" preserveAspectRatio="none"><polyline points="2,3 16,17 2,31" fill="none" stroke="var(--blue)" stroke-width="3"/><polyline points="194,3 180,17 194,31" fill="none" stroke="var(--blue)" stroke-width="3"/><line x1="10" y1="3" x2="186" y2="3" stroke="var(--blue)" stroke-width="2"/><line x1="10" y1="31" x2="186" y2="31" stroke="var(--blue)" stroke-width="2"/></svg>
      <span>Double Patty Add 4</span>
    </div>
    <div class="item" style="top:121px"><div class="line"><span>Classic Beef</span><span class="dots"></span><span>8.9</span></div><p>Shredded Lettuce, Sliced Tomato, Caramelised Onions, Beetroot And Bbq Sauce On A Buttered Sesame Seed Bun.</p></div>
    <div class="item" style="top:212px"><div class="line"><span>Cheese Burger</span><span class="dots"></span><span>9.5</span></div><p>Dill Pickles, Minced Onion, American Cheese, Mustard And Ketchup On A Soft Milk Bun.</p></div>
    <div class="item" style="top:281px"><div class="line"><span>Flame Grill</span><span class="dots"></span><span>9.5</span></div><p>Shredded Lettuce, Sliced Tomato, Minced Onion, Dill Pickles, American Cheese, Mayo And Ketchup On A Soft Milk Bun.</p></div>
    <div class="item" style="top:361px"><div class="line"><span>Big Rus</span><span class="dots"></span><span>9.9</span></div><p>Shredded Lettuce, Dill Pickles, Minced Onion, American Cheese And Special Sauce On A Soft Milk Bun.</p></div>
    <div class="item" style="top:440px"><div class="line"><span>Truffled</span><span class="dots"></span><span>9.9</span></div><p>Rocket, Caramelised Onion, Dill Pickles, Havarti Cheese And Truffle Infused Mayo On A Soft Milk Bun.</p></div>
  </section>

  <section class="column chicken">
    <p class="intro">All Our Chicken Burger Patties Are Prepared Onsite Daily Using Premium Quality Chicken Breast.</p>
    <div class="double">
      <svg viewBox="0 0 196 34" preserveAspectRatio="none"><polyline points="2,3 16,17 2,31" fill="none" stroke="var(--blue)" stroke-width="3"/><polyline points="194,3 180,17 194,31" fill="none" stroke="var(--blue)" stroke-width="3"/><line x1="10" y1="3" x2="186" y2="3" stroke="var(--blue)" stroke-width="2"/><line x1="10" y1="31" x2="186" y2="31" stroke="var(--blue)" stroke-width="2"/></svg>
      <span>Double Patty Add 4</span>
    </div>
    <div class="item" style="top:121px"><div class="line"><span>Classic Chicken</span><span class="dots"></span><span>8.9</span></div><p>Shredded Lettuce, Cheese And Mayo On A Classic Sesame Seed Bun.</p></div>
    <div class="item" style="top:195px"><div class="line"><span>Pirri Pirri</span><span class="dots"></span><span>9.5</span></div><p>Shredded Lettuce, Cheese Mayo And House Made Pirri Pirri On A Classic Sesame Seed Bun.</p></div>
    <div class="item" style="top:278px"><div class="line"><span>Kentucky</span><span class="dots"></span><span>9.9</span></div><p>Shredded Lettuce, Swiss Cheese And Feisty Mayo On A Soft Milk Bun.</p></div>
    <div class="item" style="top:361px"><div class="line"><span>El Burger</span><span class="dots"></span><span>9.9</span></div><p>Shredded Lettuce, Salsa, Guacamole, Cheese And Chipotle Mayo On A Classic Sesame Seed Bun.</p></div>
  </section>

  <svg class="abs side-band" viewBox="0 0 629 187" preserveAspectRatio="none" aria-hidden="true"><path d="M60,20 L629,0 L629,170 L300,187 L120,160 L20,120 L0,90 L80,100 Z" fill="var(--blue-deep)"/></svg>
  <div class="abs side-badge">SIDE</div>
  <div class="abs side-list">
    <div class="line"><span>Fries</span><span class="dots"></span><span>3.5</span></div>
    <div class="line"><span>Kentucky Tenders</span><span class="dots"></span><span>6.9</span></div>
    <p>Breaded and fried chicken tenders with secret seasoning. (2pcs)</p>
  </div>

  <div class="abs stars" style="left:570px;top:190px;width:80px;height:308px" role="img" aria-label="Hand-drawn blue stars"></div>
  <div class="abs stars orange" style="left:360px;top:560px;width:136px;height:76px" role="img" aria-label="Hand-drawn orange stars"></div>
  <div class="abs stars orange" style="left:1114px;top:560px;width:68px;height:80px" role="img" aria-label="Hand-drawn orange stars"></div>

  <div class="abs brand"><span class="dot"></span><span>Rustle Burger</span></div>

  <h2 class="abs heading nachos-title">NACHOS &amp; LOADED FRIES</h2>
  <div class="box choice" style="left:665px;top:284px;width:244px;height:159px">
    <div class="step-title">Choose Either</div>
    <div class="step">STEP<br>ONE</div>
    <div class="line"><span>Seasoned Fries</span><span class="dots"></span><span>9.9</span></div>
    <div class="line"><span>or Freshly Cooked</span></div>
    <div class="line"><span>Corn Chips</span><span class="dots"></span><span>11.5</span></div>
  </div>
  <div class="box loaded" style="left:926px;top:284px;width:244px;height:159px">
    <div class="step-title">Choose One</div>
    <div class="step">STEP<br>TWO</div>
    <p><b>Guacamole</b> salsa fresca, guacamole, jalapenos, cheese sauce and sour cream.</p>
    <p style="margin-top:6px"><b>Beef</b> chilli salsa fresca, beef chilli, jalapenos, cheese sauce and sour cream.</p>
  </div>

  <h2 class="abs heading ribs-title">BUFFALO CHICKEN RIBS</h2>
  <p class="abs ribs-copy">Buffalow style fried chicken ribs smothered in one our mouth-watering sauces, served with a side of ranch sauce.</p>
  <div class="box packs" style="left:735px;top:553px;width:181px;height:102px">
    <div class="line"><span>6 Pack</span><span class="dots"></span><span>6.9</span></div>
    <div class="line"><span>12 Pack</span><span class="dots"></span><span>12.9</span></div>
    <div class="line"><span>24 Pack</span><span class="dots"></span><span>23.9</span></div>
  </div>
  <div class="box sauces" style="left:934px;top:553px;width:169px;height:102px">Classic Hot Sauce<br>or Smoky BBQ</div>

</main>
</body>
</html>
```